Aunt Roula's Bakery

I am about to create a luxury boutique that specializes in cake baking and cupcake
and ready for parties and special events and order delivery
the logo has already made

Boutique

Email:auntroulasbakery@mailbox-example.net
Instagram: aunt_roula_bakery
Twitter: xxxxxxx
WhatsApp: xxxxxxx

Requirements
Must have
• luxury design

```html
<!DOCTYPE html>
<html lang="en">
<head>
<meta charset="utf-8">
<title>Aunt Roula's Bakery – Business Card</title>
<link rel="stylesheet" href="https://fonts.googleapis.com/css2?family=Arimo:wght@400;700&display=swap">
<style>
  :root {
    --backdrop: #4a413c;
    --card: #161616;
    --card-edge: #222;
    --silver: #b9b9b9;
    --silver-dim: #8a8a8a;
    --pink: #e9a3b6;
    --white: #f2f2f2;
    --rule: #9a9a9a;
  }
  * { box-sizing: border-box; margin: 0; padding: 0; }
  html, body { width: 1200px; height: 787px; overflow: hidden; }
  body {
    background: var(--backdrop);
    font-family: "Arimo", Arial, sans-serif;
    display: flex;
    align-items: center;
    justify-content: center;
    gap: 40px;
  }
  .card {
    width: 520px;
    height: 297px;
    background: var(--card);
    border: 1px solid var(--card-edge);
    border-radius: 4px;
    position: relative;
    box-shadow: 0 10px 24px rgba(0,0,0,.35);
  }
  /* front */
  .card-front .brand {
    position: absolute;
    left: 60px; top: 62px;
    width: 260px;
    display: flex; flex-direction: column; align-items: center; gap: 14px;
  }
  .brand-dot {
    width: 46px; height: 46px; border-radius: 50%;
  }
  .card-front .brand-dot { background: var(--silver-dim); }
  .brand-name {
    font-weight: 700;
    font-size: 26px;
    letter-spacing: 2px;
    text-transform: uppercase;
    text-align: center;
    line-height: 1.25;
  }
  .card-front .brand-name { color: var(--silver); }
  .website {
    position: absolute;
    left: 80px; bottom: 52px;
    color: var(--silver-dim);
    font-size: 12px;
    letter-spacing: 3px;
  }
  /* back */
  .card-back .brand {
    position: absolute;
    left: 28px; top: 70px;
    width: 200px;
    display: flex; flex-direction: column; align-items: center; gap: 12px;
  }
  .card-back .brand-dot { background: var(--pink); width: 40px; height: 40px; }
  .card-back .brand-name { color: var(--pink); font-size: 21px; }
  .divider {
    position: absolute;
    left: 250px; top: 50px; bottom: 50px;
    width: 1px; background: var(--rule);
  }
  .contact {
    position: absolute;
    left: 272px; top: 72px;
  }
  .person-name { color: var(--pink); font-weight: 700; font-size: 19px; }
  .person-role { color: var(--white); font-size: 14px; margin: 3px 0 14px; }
  .contact-list { list-style: none; }
  .contact-item {
    display: flex; align-items: center; gap: 8px;
    color: var(--white); font-size: 12.5px; margin-bottom: 5px;
    white-space: nowrap;
  }
  .contact-icon { width: 13px; height: 13px; flex: none; }
  .social-dot { width: 11px; height: 11px; border-radius: 50%; background: var(--pink); margin: 0 1px; flex: none; }
</style>
</head>
<body>
  <section class="card card-front">
    <div class="brand">
      <span class="brand-dot"></span>
      <span class="brand-name">Aunt Roula's Bakery</span>
    </div>
    <p class="website">www.auntroulas.example</p>
  </section>

  <section class="card card-back">
    <div class="brand">
      <span class="brand-dot"></span>
      <span class="brand-name">Aunt Roula's Bakery</span>
    </div>
    <span class="divider"></span>
    <div class="contact">
      <p class="person-name">Rami Haddad</p>
      <p class="person-role">President</p>
      <ul class="contact-list">
        <li class="contact-item">
          <svg class="contact-icon" viewBox="0 0 24 24" aria-hidden="true"><path fill="#e9a3b6" d="M6.6 10.8a15 15 0 0 0 6.6 6.6l2.2-2.2a1 1 0 0 1 1-.25 11.4 11.4 0 0 0 3.6.57 1 1 0 0 1 1 1V20a1 1 0 0 1-1 1A17 17 0 0 1 3 4a1 1 0 0 1 1-1h3.5a1 1 0 0 1 1 1c0 1.25.2 2.45.57 3.57a1 1 0 0 1-.25 1z"/></svg>
          555 0142 7788
        </li>
        <li class="contact-item">
          <svg class="contact-icon" viewBox="0 0 24 24" aria-hidden="true"><path fill="#e9a3b6" d="M2 5h20v14H2z"/><path fill="none" stroke="#161616" stroke-width="2" d="M2 5l10 8 10-8"/></svg>
          auntroulasbakery@mailbox-example.net
        </li>
        <li class="contact-item"><span class="social-dot"></span>aunt_roula_bakery</li>
        <li class="contact-item"><span class="social-dot"></span>aunt_roula_bakery</li>
        <li class="contact-item"><span class="social-dot"></span>auntroulasbakery.chat</li>
      </ul>
    </div>
  </section>
</body>
</html>
```